Front page on www.brightmarkgoods.com modern service ads - each ad for each featured service

We need to have initial 5 banners to be created for our soon to be launched new site,. These are 5 rotating banners that will showcase our companies key features. We are looking for a modern stylish yet simple look to highlight these features. Something thats very inviting and modern to fit the look of the new website.

5 banners need to be, information can be found on www.brightmarkgoods.com about these. Please ask if any questions

Why us?
Art Services
Order Process
Current promotions
Clearance products

please also note. the design will be going onto this website. http://new.brightmarkgoods.com/ Please base actual designs , color schemes etc.. for the new site.

Target Market(s)

Small businesses that purchase marketing promotional goods, to promote their business

Industry/Entity Type

Promotional Product

Font styles to use
Sans Serif

Requirements
Must have
• Size of the banner is 965 x 400 px
Nice to have
• Modern elements,, very clean and minimal look
Should not have
• no cheap generic clip art

```html
<!DOCTYPE html>
<html lang="en">
<head>
<meta charset="utf-8">
<title>Artwork – Full Art Services</title>
<link rel="stylesheet" href="https://fonts.googleapis.com/css2?family=Montserrat:wght@700;800&display=swap">
<style>
  :root {
    --lavender: #9299d5;
    --lavender-light: #acb1e1;
    --lavender-pale: #c9caf0;
    --navy: #283061;
    --white: #ffffff;
    --icon-faint: rgba(255, 255, 255, 0.35);
  }
  html, body {
    margin: 0;
    padding: 0;
    overflow: hidden;
    background: var(--white);
  }
  .banner {
    position: relative;
    width: 1200px;
    height: 497px;
    overflow: hidden;
    font-family: "Montserrat", Arial, sans-serif;
  }
  .banner__backdrop {
    position: absolute;
    inset: 0;
    width: 1200px;
    height: 497px;
  }
  .banner__title {
    position: absolute;
    left: 0;
    right: 0;
    top: 92px;
    margin: 0;
    text-align: center;
    color: var(--white);
    font-weight: 800;
    font-size: 126px;
    line-height: 1;
    letter-spacing: 1px;
  }
  .banner__title-mark {
    display: inline-block;
    width: 100px;
    height: 100px;
    margin: 0 2px;
    vertical-align: -4px;
  }
  .banner__features {
    position: absolute;
    left: 0;
    right: 0;
    top: 244px;
    margin: 0;
    padding: 0;
    list-style: none;
    text-align: center;
    color: var(--white);
    font-weight: 800;
    font-size: 33px;
    line-height: 1;
  }
  .banner__feature {
    display: block;
    height: 55px;
    line-height: 55px;
  }
  .banner__feature span {
    display: inline-block;
    padding: 0 14px;
  }
  .banner__feature--highlight span {
    background: var(--lavender-pale);
    height: 50px;
    line-height: 52px;
  }
  .banner__feature--last span {
    height: 58px;
    line-height: 58px;
  }
</style>
</head>
<body>
  <section class="banner">
    <svg class="banner__backdrop" viewBox="0 0 965 400" aria-hidden="true">
      <defs>
        <linearGradient id="bgGradient" x1="0" y1="0" x2="1" y2="0">
          <stop offset="0" stop-color="#abb0e0"/>
          <stop offset="1" stop-color="#8d94d2"/>
        </linearGradient>
      </defs>
      <rect width="965" height="400" fill="url(#bgGradient)"/>
      <!-- lighter diagonal band -->
      <polygon points="0,210 520,-60 700,-60 0,330" fill="#a3a8dd" opacity="0.55"/>
      <polygon points="300,400 965,60 965,160 500,400" fill="#a5aade" opacity="0.5"/>
      <!-- white corners -->
      <polygon points="0,0 395,0 0,205" fill="var(--white)"/>
      <polygon points="965,128 965,400 600,400" fill="var(--white)"/>
      <!-- top-left shapes -->
      <rect x="-60" y="70" width="150" height="36" rx="18" fill="var(--navy)" transform="rotate(-28 15 88)"/>
      <rect x="300" y="-28" width="140" height="34" rx="17" fill="var(--lavender-pale)" transform="rotate(-28 370 -11)"/>
      <!-- right shapes -->
      <rect x="820" y="150" width="190" height="40" rx="20" fill="var(--navy)" transform="rotate(-28 915 170)"/>
      <rect x="690" y="340" width="220" height="42" rx="21" fill="var(--navy)" transform="rotate(-28 800 361)"/>
      <rect x="930" y="262" width="90" height="38" rx="19" fill="var(--lavender-pale)" transform="rotate(-28 975 281)"/>
      <!-- outline circles -->
      <circle cx="785" cy="-2" r="22" fill="none" stroke="var(--white)" stroke-width="4"/>
      <circle cx="62" cy="273" r="9" fill="none" stroke="var(--white)" stroke-width="3.5"/>
      <circle cx="941" cy="368" r="6" fill="none" stroke="var(--lavender-pale)" stroke-width="3"/>
      <!-- outline triangles -->
      <polygon points="311,36 327,43 314,54" fill="none" stroke="var(--white)" stroke-width="3" stroke-linejoin="round"/>
      <polygon points="905,56 920,52 914,67" fill="none" stroke="var(--navy)" stroke-width="3" stroke-linejoin="round"/>
      <polygon points="145,350 188,344 163,385" fill="none" stroke="var(--white)" stroke-width="4" stroke-linejoin="round"/>
      <!-- faint decorative icons -->
      <g role="img" aria-label="Faint drawing tablet and stylus icon">
        <rect x="100" y="190" width="90" height="62" rx="8" fill="var(--icon-faint)" transform="rotate(-25 145 221)"/>
      </g>
      <g role="img" aria-label="Faint document and pencil icon">
        <rect x="788" y="72" width="72" height="70" rx="8" fill="var(--icon-faint)" transform="rotate(20 824 107)"/>
      </g>
    </svg>

    <h1 class="banner__title">ARTW<svg class="banner__title-mark" viewBox="0 0 100 100" role="img" aria-label="Paint palette with brush icon"><circle cx="50" cy="50" r="46" fill="var(--white)"/></svg>RK</h1>

    <ul class="banner__features">
      <li class="banner__feature banner__feature--highlight"><span>FULL ART SERVICES,</span></li>
      <li class="banner__feature"><span>FREE DIGITAL PROOFS,</span></li>
      <li class="banner__feature banner__feature--highlight banner__feature--last"><span>UNLIMITED PROOF REVISIONS</span></li>
    </ul>
  </section>
</body>
</html>
```